Etiketten für Olivenöl-Intensivcreme
Zielgruppe
Wir produzieren Bio-Food, u.a. Wein und Olivenöl. Jetzt soll eine Olivenöl-Intensivcreme im Bereich Kosmetik auf dem Markt platziert werden. Unsere Zielgruppe hat ein sehr breites Altersspektrum (jung bis alt), ist naturverbunden, tierlieb, gebildet, kritisch-reflektierend, weiß gute Qualität zu schätzen, ist überwiegend weiblich. Die Olivenöl-Intensivcreme hat eine sehr breite Verwendung und soll sich als 'Allzweckwaffe' in jedem Haushalt etablieren (Babyhaut-Pflege, Lippenpflege, Ganzkörperpflege, Hand-Schutzcreme etc.).
Aufgabenstellung
Die Creme soll heißen: Velamira (es könnte z.B. der Buchstabe 'O' durch eine Olive ersetzt werden). Es gibt zwei Etikette (Deckeloberseite der Metalldose und auf dem Boden). Der Durchmesser der Etikette ist jeweils 5,5 cm. Die Deckelunterseite gilt reinen Pflichtangaben. Im Dateidownloadbereich sind die Textvorgaben für die Etikette. MUT zur Farbe! Wir sind NICHT brav und angepasst! Orange kann Akzente setzen bzw. für Aufmerksamkeit im Regal sorgen.

```html
<!DOCTYPE html>
<html lang="de">
<head>
<meta charset="utf-8">
<title>Velamira – Etiketten Entwurf 1</title>
<link rel="stylesheet" href="https://fonts.googleapis.com/css2?family=Fira+Sans+Condensed:wght@300;400;600&family=Courier+Prime:wght@700&display=swap">
<style>
  :root {
    --sheet-light: #fbfbfb;
    --sheet-grey: #c8c8c8;
    --ink: #2d2d2d;
    --peach: #fdd9a0;
    --orange: #f39418;
    --orange-deep: #ee8f12;
    --green: #a1ab3a;
    --green-light: #e7e4b6;
    --olive-dark: #4f5e1e;
    --olive-text: #8d8a45;
    --olive-fruit: #4a4316;
    --pale: #ebeab3;
    --cream: #fff3d0;
    --forest: #4a6a26;
    --white: #ffffff;
  }
  * { margin: 0; padding: 0; box-sizing: border-box; }
  html, body { width: 900px; height: 1200px; overflow: hidden; }
  body {
    position: relative;
    background: linear-gradient(115deg, var(--sheet-grey) 0%, var(--sheet-light) 55%, #e2e2e2 100%);
    font-family: "Fira Sans Condensed", sans-serif;
    color: var(--ink);
  }
  .sheet-title, .variant-title {
    position: absolute;
    font-weight: 400;
    transform: translateX(-50%);
    white-space: nowrap;
  }
  .sheet-title { left: 450px; top: 50px; font-size: 19px; }
  .variant-title { top: 76px; font-size: 19px; }
  .variant-a { left: 287px; }
  .variant-b { left: 615px; }
  .label {
    position: absolute;
    width: 292px;
    height: 292px;
  }
  .label-a-front { left: 139px; top: 190px; }
  .label-b-front { left: 468px; top: 190px; }
  .label-a-back  { left: 139px; top: 500px; }
  .label-b-back  { left: 468px; top: 500px; }
  .label text { font-family: "Fira Sans Condensed", sans-serif; }
  .arc-text { font-family: "Courier Prime", monospace; font-weight: 700; font-size: 30px; fill: var(--cream); letter-spacing: 1px; }
  .brand-name { font-weight: 400; }
  .mono { font-family: "Courier Prime", monospace !important; font-weight: 700; }
</style>
</head>
<body>
  <h1 class="sheet-title">ENTWURF 1</h1>
  <h2 class="variant-title variant-a">variante A</h2>
  <h2 class="variant-title variant-b">variante B</h2>

  <!-- Variante A, Deckel -->
  <svg class="label label-a-front" viewBox="-270 -270 540 540" aria-label="Deckeletikett Variante A">
    <defs>
      <radialGradient id="greenGlowA" cx="0.5" cy="0.3" r="0.7">
        <stop offset="0" stop-color="var(--green-light)"/>
        <stop offset="0.55" stop-color="var(--green)"/>
      </radialGradient>
      <clipPath id="innerA"><circle r="258"/></clipPath>
      <path id="arcA" d="M -222 0 A 222 222 0 0 1 222 0"/>
    </defs>
    <circle r="270" fill="var(--peach)"/>
    <g clip-path="url(#innerA)">
      <rect x="-270" y="-270" width="540" height="540" fill="var(--peach)"/>
      <rect x="-270" y="-238" width="540" height="140" fill="url(#greenGlowA)"/>
      <rect x="-110" y="-195" width="220" height="18" fill="var(--orange)"/>
      <rect x="-270" y="48" width="540" height="176" fill="var(--green)"/>
      <rect x="-120" y="232" width="240" height="16" fill="var(--orange)"/>
    </g>
    <text class="arc-text"><textPath href="#arcA" startOffset="50%" text-anchor="middle">Vegane Naturkosmetik aus Bio-Oliven</textPath></text>
    <circle cx="-100" cy="-35" r="88" fill="var(--olive-fruit)" stroke="var(--orange)" stroke-width="12"/>
    <text class="brand-name" x="-5" y="22" font-size="86" fill="#eea040" textLength="250" lengthAdjust="spacingAndGlyphs">Velamira</text>
    <text x="-228" y="90" font-size="28" fill="var(--olive-dark)">Pflege- und Schutzcreme</text>
    <text x="52" y="96" font-size="40" fill="var(--olive-dark)" letter-spacing="2">OLIVENÖL-</text>
    <text x="52" y="138" font-size="40" fill="var(--white)" letter-spacing="2">INTENSIV</text>
    <text x="52" y="180" font-size="40" fill="var(--olive-dark)" letter-spacing="2">CREME</text>
    <rect x="-30" y="108" width="56" height="70" rx="10" fill="#c8c373" opacity="0.7" role="img" aria-label="Illustration eines galoppierenden Pferdes"/>
    <text x="0" y="210" font-size="30" font-weight="300" fill="var(--cream)" text-anchor="middle" letter-spacing="1">KORVEN.LAND</text>
  </svg>

  <!-- Variante B, Deckel -->
  <svg class="label label-b-front" viewBox="-270 -270 540 540" aria-label="Deckeletikett Variante B">
    <defs>
      <clipPath id="innerB"><circle r="258"/></clipPath>
      <path id="arcB" d="M -222 0 A 222 222 0 0 1 222 0"/>
    </defs>
    <circle r="270" fill="var(--pale)"/>
    <g clip-path="url(#innerB)">
      <rect x="-270" y="-270" width="540" height="540" fill="var(--orange)"/>
      <rect x="-130" y="-200" width="260" height="44" fill="var(--peach)"/>
      <rect x="-120" y="232" width="240" height="26" fill="var(--forest)"/>
    </g>
    <text class="arc-text"><textPath href="#arcB" startOffset="50%" text-anchor="middle">Vegane Naturkosmetik aus Bio-Oliven</textPath></text>
    <rect x="82" y="-150" width="36" height="52" rx="8" fill="#f8c98a" role="img" aria-label="Illustration eines galoppierenden Pferdes"/>
    <text x="125" y="-34" font-size="34" fill="var(--white)" text-anchor="middle" letter-spacing="1">KORVEN.LAND</text>
    <circle cx="-145" cy="0" r="72" fill="var(--olive-fruit)" stroke="var(--pale)" stroke-width="10"/>
    <text class="brand-name" x="-62" y="68" font-size="84" fill="var(--olive-text)" textLength="292" lengthAdjust="spacingAndGlyphs">Velamira</text>
    <text x="58" y="112" font-size="28" fill="var(--white)" text-anchor="middle">Pflege- und Schutzcreme</text>
    <text x="10" y="162" font-size="40" text-anchor="middle" letter-spacing="2"><tspan fill="var(--olive-dark)">OLIVENÖL-</tspan><tspan fill="var(--white)">INTENSIV</tspan></text>
    <text x="10" y="204" font-size="40" fill="var(--olive-dark)" text-anchor="middle" letter-spacing="2">CREME</text>
  </svg>

  <!-- Variante A, Boden -->
  <svg class="label label-a-back" viewBox="-270 -270 540 540" aria-label="Bodenetikett Variante A">
    <defs>
      <radialGradient id="greenGlowA2" cx="0.45" cy="0.4" r="0.6">
        <stop offset="0" stop-color="var(--green-light)"/>
        <stop offset="1" stop-color="var(--green)"/>
      </radialGradient>
      <clipPath id="innerA2"><circle r="258"/></clipPath>
    </defs>
    <circle r="270" fill="var(--peach)"/>
    <g clip-path="url(#innerA2)">
      <rect x="-270" y="-245" width="540" height="462" fill="url(#greenGlowA2)"/>
      <rect x="-110" y="-208" width="220" height="18" fill="var(--orange)"/>
      <rect x="-130" y="228" width="260" height="30" fill="var(--orange)"/>
    </g>
    <circle cx="-195" cy="-28" r="34" fill="var(--olive-fruit)" stroke="var(--orange)" stroke-width="6"/>
    <text class="brand-name" x="-158" y="-8" font-size="44" fill="#eea040" textLength="92" lengthAdjust="spacingAndGlyphs">Velamira</text>
    <text x="-240" y="18" font-size="21" fill="var(--olive-dark)">Wasserfreie Creme</text>
    <text x="-240" y="42" font-size="21" fill="var(--olive-dark)">unparfümiert</text>
    <text x="-232" y="90" font-size="24" font-weight="600" fill="var(--white)">150ml</text>
    <rect x="-150" y="75" width="70" height="150" rx="20" fill="#ece3a0" opacity="0.55" role="img" aria-label="Illustration eines galoppierenden Pferdes"/>
    <text x="-65" y="-176" font-size="20" font-weight="600" fill="var(--white)" letter-spacing="1">ANWENDUNG:</text>
    <g font-size="20" fill="var(--olive-dark)">
      <text x="-65" y="-154" textLength="130" lengthAdjust="spacing">Sparsam auf die</text>
      <text x="-65" y="-132" textLength="130" lengthAdjust="spacing">trockene Haut</text>
      <text x="-65" y="-110" textLength="130" lengthAdjust="spacing">auftragen (die</text>
      <text x="-65" y="-88" textLength="130" lengthAdjust="spacing">Creme ist sehr</text>
      <text x="-65" y="-66" textLength="130" lengthAdjust="spacing">ergiebig!). Die</text>
      <text x="-65" y="-44" textLength="130" lengthAdjust="spacing">Einwirkzeit kann</text>
      <text x="-65" y="-22" textLength="130" lengthAdjust="spacing">einige Minuten</text>
      <text x="-65" y="0" textLength="130" lengthAdjust="spacing">dauern. Vorher</text>
      <text x="-65" y="22" textLength="130" lengthAdjust="spacing">kann es beim</text>
      <text x="-65" y="44" textLength="130" lengthAdjust="spacing">Berühren von</text>
      <text x="-65" y="66" textLength="130" lengthAdjust="spacing">Gegenständen</text>
      <text x="-65" y="88" textLength="130" lengthAdjust="spacing">mit den gecrem-</text>
      <text x="-65" y="110" textLength="130" lengthAdjust="spacing">ten Körperpartien</text>
      <text x="-65" y="132" textLength="130" lengthAdjust="spacing">zur Fettübertra-</text>
      <text x="-65" y="154" textLength="130" lengthAdjust="spacing">gung kommen.</text>
    </g>
    <g font-size="17" fill="var(--olive-dark)" font-weight="300">
      <text x="92" y="-152">Ingredients:</text>
      <text x="92" y="-132">Olea Europaea</text>
      <text x="92" y="-112">Friut Oil, Hydro-</text>
      <text x="92" y="-92">genated Rapeseed</text>
      <text x="92" y="-72">Oil, Tocopherol</text>
    </g>
    <rect x="92" y="-40" width="152" height="48" fill="var(--peach)"/>
    <text x="100" y="-18" font-size="17" fill="var(--olive-dark)">Mindestens haltbar:</text>
    <text class="mono" x="100" y="2" font-size="15" fill="var(--ink)">JANUAR 2021</text>
    <g font-size="17" fill="var(--olive-dark)" font-weight="300">
      <text x="92" y="42">KORVEN.LAND</text>
      <text x="92" y="62">Dr. med. Lena Holmer</text>
      <text x="92" y="82">Hafenweg 42</text>
      <text x="92" y="102">D - 24103 Kiel</text>
      <text x="92" y="122">www.korven.land</text>
    </g>
    <g transform="translate(123 172)" fill="none" stroke="var(--olive-dark)" stroke-width="9" stroke-linejoin="round" role="img" aria-label="Recycling-Symbol">
      <path d="M 0 -24 L 22 14 L -22 14 Z"/>
    </g>
    <text x="-65" y="204" font-size="20" fill="var(--white)">Made in Germany</text>
  </svg>

  <!-- Variante B, Boden -->
  <svg class="label label-b-back" viewBox="-270 -270 540 540" aria-label="Bodenetikett Variante B">
    <defs>
      <clipPath id="innerB2"><circle r="258"/></clipPath>
    </defs>
    <circle r="270" fill="var(--pale)"/>
    <g clip-path="url(#innerB2)">
      <rect x="-270" y="-270" width="540" height="490" fill="var(--orange-deep)"/>
      <rect x="-120" y="224" width="240" height="34" fill="var(--orange)"/>
    </g>
    <circle cx="-40" cy="-203" r="36" fill="var(--olive-fruit)" stroke="var(--pale)" stroke-width="6"/>
    <text class="brand-name" x="-2" y="-180" font-size="44" fill="var(--olive-text)" textLength="110" lengthAdjust="spacingAndGlyphs">Velamira</text>
    <rect x="-122" y="-180" width="68" height="170" rx="22" fill="#f8c98a" opacity="0.8" role="img" aria-label="Illustration eines galoppierenden Pferdes"/>
    <text x="-34" y="-136" font-size="24" font-weight="600" fill="var(--white)">150ml</text>
    <text x="41" y="-148" font-size="21" fill="#f7ecb8">Wasserfreie Creme</text>
    <text x="41" y="-126" font-size="21" fill="#f7ecb8">unparfümiert</text>
    <g font-size="17" fill="#f7ecb8" font-weight="300">
      <text x="41" y="-96">Ingredients:</text>
      <text x="41" y="-76">Olea Europaea Friut Oil,</text>
      <text x="41" y="-56">Hydrogenated Rapeseed Oil,</text>
      <text x="41" y="-36">Tocopherol</text>
    </g>
    <text x="-230" y="-16" font-size="21" font-weight="600" fill="var(--olive-dark)">ANWENDUNG:</text>
    <g font-size="18" fill="var(--white)" text-anchor="middle">
      <text x="0" y="6" textLength="470" lengthAdjust="spacingAndGlyphs">Sparsam auf die trockene Haut auftragen (Creme ist sehr ergiebig!).</text>
      <text x="0" y="27">Die Einwirkzeit kann einige Minuten dauern.</text>
      <text x="0" y="48">Vorher kann es beim Berühren von Gegenständen mit den</text>
      <text x="0" y="69">gecremten Körperpartien zur Fettübertragung kommen.</text>
    </g>
    <text x="-46" y="113" font-size="17" fill="var(--white)" text-anchor="end">Mindestens haltbar:</text>
    <rect x="-36" y="90" width="216" height="36" fill="var(--pale)"/>
    <text class="mono" x="72" y="114" font-size="15" fill="var(--ink)" text-anchor="middle">JANUAR 2021</text>
    <g font-size="17" fill="var(--white)" font-weight="300" text-anchor="middle">
      <text x="0" y="150">KORVEN.LAND</text>
      <text x="0" y="170">Dr. med. Lena Holmer</text>
      <text x="0" y="190">Hafenweg 42, D - 24103 Kiel</text>
      <text x="0" y="210">www.korven.land</text>
    </g>
    <g transform="translate(138 172)" fill="none" stroke="var(--forest)" stroke-width="9" stroke-linejoin="round" role="img" aria-label="Recycling-Symbol">
      <path d="M 0 -24 L 22 14 L -22 14 Z"/>
    </g>
    <text x="0" y="250" font-size="18" fill="var(--olive-dark)" text-anchor="middle">Made in Germany</text>
  </svg>
</body>
</html>
```